Maranoola Wines - web page for new Australian wine label

We need a landing page for our wine company. Maranoola is a family owned company, we grow the gapes, and make the wine in the Clare valley. Daniel Whitlock is the winemaker and is well known for his style, which is all about the fruit flavour rather than wood or age influences. Maranoola is Abriginal for 2 hills and a water source. We hand pick, hand plunge, foot crush resulting in elegant wine. Little to no additives, minimal filtering, single vineyard wines. Handcrafted with small releases of only the best fruit from carefully selected rows and bunches. The Clare valley is located two hours North of Adelaide, is known for cool climate and slow ripening, resulting in wines that have an elegant mouth feel, with bright colour and outstanding flavours. Our Brookmere vineyard has a Eastern aspect, gathering morning sun and escaping the hot afternoons, and in our opinion is on of the prettiest valleys in the world. Only 1000 cases per annum of the very best handpicked fruit, from the best rows. We hope you enjoy the Maranoola style, the reds are lighter in colour, fruit driven palate, more old world influence and the Riesling is on the dry side with fresh citrus. Minimal additives and filtering, our aim was to make wine with minimal influence from wine making. Handcrafted wines.

Target Market(s)

females 18 - 60 are the ones that buy 70 percent of wine, so whilst men are also a target, its the ladies we seek to appeal to.

Industry/Entity Type

It Company

Number of Pages Required

4 page

Font styles to use
Serif

Requirements
Must have
• Eye catching front page that makes me feel like i am ordering from quality company, that cares for what they do. Easy to use ordering, and delivery instructions.
• postage is $14.90 per case Australia wide.
• www.maranoolawines-example.com
Nice to have
• I want to see a fun and family oriented business that cares for the wine, we dont make a lot, its buckets and feet. But its wine made wanting to be the best in the world, we dont cut corners on quality. Handcrafted
Should not have
• dont really have any thoughts here, looking for all ideas

```html
<!DOCTYPE html>
<html lang="en">
<head>
<meta charset="utf-8">
<title>Maranoola Wines</title>
<link href="https://fonts.googleapis.com/css2?family=Open+Sans:wght@400;600&family=Roboto+Condensed:wght@400;700&display=swap" rel="stylesheet">
<style>
:root{
  --blue:#1f63b8;
  --blue-deep:#0f3d96;
  --ink:#222;
  --text:#555;
  --muted:#777;
  --line:#e2e2e2;
  --white:#fff;
  --price:#ff5a3c;
}
*{box-sizing:border-box;margin:0;padding:0}
html,body{width:1200px;height:3358px;overflow:hidden}
body{font-family:"Open Sans",Arial,sans-serif;color:var(--text);background:var(--white);position:relative;font-size:12px;line-height:1.7}
h1,h2,h3,h4,.nav a,.btn,.brand{font-family:"Roboto Condensed","Arial Narrow",sans-serif}
.section{position:absolute;left:0;width:1200px}

/* header */
.site-header{top:0;height:96px;background:var(--white)}
.brand{position:absolute;left:98px;top:26px;font-size:40px;color:var(--blue);font-weight:400;line-height:1}
.nav{position:absolute;right:98px;top:38px;display:flex;gap:24px}
.nav a{font-size:13px;color:#333;text-decoration:none;text-transform:uppercase;letter-spacing:.2px;position:relative}
.nav a.active{color:var(--blue)}
.nav a.active::after{content:"";position:absolute;left:50%;top:44px;margin-left:-9px;border:9px solid transparent;border-bottom-color:var(--blue);border-top:0}

/* hero */
.hero{top:96px;height:576px;overflow:hidden}
.hero-photo{position:absolute;inset:0;background:linear-gradient(180deg,#d9751c 0%,#f0a93a 22%,#a2611d 38%,#5c4a1d 55%,#3c3517 80%,#2c2a14 100%)}
.hero-bottles{position:absolute;left:634px;top:100px;width:210px;height:356px;background:linear-gradient(90deg,#2a0c0c,#4a1515 50%,#2a0c0c);border-radius:12px 12px 6px 6px}
.hero-badge{position:absolute;left:786px;top:130px;width:314px;height:314px;border-radius:50%;background:rgba(31,99,184,.88);border:6px solid rgba(255,255,255,.35);text-align:center;color:var(--white);padding-top:70px}
.hero-badge .brand-name{font-family:"Roboto Condensed",sans-serif;font-size:40px;line-height:1}
.hero-badge p{font-size:13px;line-height:1.5;width:214px;margin:12px auto 16px}
.btn{display:inline-block;text-transform:uppercase;font-size:13px;text-decoration:none;color:var(--white);padding:7px 18px;border:1px solid rgba(255,255,255,.8);border-radius:3px}
.hero-wave{position:absolute;left:0;bottom:0}

/* welcome */
.welcome{top:720px;text-align:center}
.section-title{font-size:34px;color:var(--ink);font-weight:400;text-transform:uppercase;letter-spacing:.5px}
.welcome .lead{width:870px;margin:18px auto 0;font-size:11.5px;line-height:1.75}
.features{display:flex;justify-content:center;gap:64px;margin-top:44px}
.feature{width:280px}
.feature svg{display:block;margin:0 auto 14px}
.feature h3{font-size:19px;color:var(--blue);font-weight:400;text-transform:uppercase;margin-bottom:10px}
.feature p{font-size:11px;line-height:1.8}

/* delivery */
.delivery{top:1157px;height:388px;text-align:center;color:var(--white)}
.delivery-photo{position:absolute;inset:0;background:radial-gradient(ellipse at 50% 30%,#3a2f24 0%,#1c1712 55%,#0f0c09 100%)}
.delivery-inner{position:relative;padding-top:110px}
.delivery h2{font-size:38px;line-height:1.25;font-weight:700;text-transform:uppercase}
.delivery h2 .price{color:var(--price)}
.delivery p{width:860px;margin:18px auto 22px;font-size:11.5px;line-height:1.75;color:#ddd}

/* products */
.products{top:1645px;height:290px}
.product-photo{position:absolute;left:98px;top:0;width:402px;height:288px;border:1px solid #ccc;background:linear-gradient(120deg,#e9eef2 0%,#cfd6db 40%,#9b2a1e 52%,#d7dde2 62%,#eef1f3 100%)}
.product-body{position:absolute;left:533px;top:10px;width:570px}
.product-body h2{font-size:33px;color:var(--ink);font-weight:400;text-transform:uppercase}
.product-body p{font-size:11px;line-height:1.85;margin-top:10px}
.tick-list{display:grid;grid-template-columns:1fr 1fr;gap:2px 20px;list-style:none;margin:12px 0 20px;font-size:11px}
.tick-list li{display:flex;align-items:center;gap:8px}
.btn-solid{background:var(--blue);border-color:var(--blue);padding:8px 28px;border-radius:2px}

/* why us */
.why{top:2033px;height:475px;background:linear-gradient(90deg,#d9d9d9,#e8e8e8 50%,#d6d6d6);text-align:center}
.why .section-title{padding-top:46px;font-size:32px}
.cards{position:absolute;top:119px;left:98px;display:flex;gap:27px}
.card{width:316px;height:288px;background:var(--white);box-shadow:0 1px 3px rgba(0,0,0,.15)}
.card-photo{height:200px}
.card h3{font-size:19px;color:var(--ink);font-weight:400;margin-top:12px}
.card p{font-size:11px;line-height:1.7;padding:4px 20px 0}

/* gallery & news */
.gallery-news{top:2585px;height:340px}
.block-title{font-size:24px;color:var(--ink);font-weight:400;text-transform:uppercase}
.gallery-title{position:absolute;left:98px;top:0}
.news-title{position:absolute;left:797px;top:0}
.gallery-grid{position:absolute;left:98px;top:53px}
.thumb{position:absolute;left:0;width:180px;height:90px}
.feature-shot{position:absolute;left:189px;top:0;width:464px;height:284px}
.news{position:absolute;left:797px;top:53px;width:313px}
.news-item{display:flex;gap:14px;padding-bottom:14px;margin-bottom:14px;border-bottom:1px solid var(--line)}
.news-photo{width:110px;height:130px;flex:none}
.news-item h4{font-family:"Open Sans",sans-serif;font-size:13px;color:var(--blue);font-weight:600}
.news-date{display:flex;align-items:center;gap:6px;color:var(--blue);font-size:11.5px;margin:6px 0}
.news-item p{font-size:11.5px;line-height:1.75}

/* footer */
.site-footer{top:3005px;height:353px;background:var(--blue-deep);color:var(--white)}
.footer-col{position:absolute;top:42px}
.footer-brand{font-family:"Roboto Condensed",sans-serif;font-size:40px;line-height:1;color:var(--white)}
.footer-address{font-size:12px;line-height:1.6;margin-top:20px}
.contact-row{display:flex;gap:14px;align-items:flex-start;font-size:12px;line-height:1.6;margin-top:12px}
.footer-col h4{font-size:20px;font-weight:400;text-transform:uppercase;margin-top:20px;margin-bottom:14px;letter-spacing:.4px}
.quick-links{list-style:none;font-size:12px;line-height:1.85}
.quick-links li::before{content:"";display:inline-block;border:4px solid transparent;border-left:5px solid var(--white);margin-right:10px}
.newsletter p{font-size:11.5px;line-height:1.6;width:230px}
.field{width:286px;height:42px;background:var(--white);color:#444;font-size:11px;padding:12px;margin:18px 0 16px}
.btn-dark{background:#1a1a1a;border:0;padding:10px 16px;font-size:12px;border-radius:0}
.social-list{list-style:none;font-size:12.5px}
.social-list li{display:flex;align-items:center;gap:10px;margin-bottom:12px}
.dot{width:24px;height:24px;border-radius:50%;border:1px solid rgba(255,255,255,.8)}
.footer-bar{position:absolute;left:0;top:291px;width:1200px;border-top:1px solid rgba(255,255,255,.2);text-align:center;font-size:12px;padding-top:20px}
.footer-bar .page-tag{position:absolute;right:52px;top:20px}
</style>
</head>
<body>

<header class="section site-header">
  <div class="brand">Maranoola</div>
  <nav class="nav">
    <a class="active" href="#">Home</a>
    <a href="#">About Us</a>
    <a href="#">Our Services</a>
    <a href="#">Products</a>
    <a href="#">Gallery</a>
    <a href="#">Contact Us</a>
  </nav>
</header>

<section class="section hero">
  <div class="hero-photo" role="img" aria-label="Vineyard rows at sunset under a glowing orange sky"></div>
  <div class="hero-bottles" role="img" aria-label="Three bottles of Maranoola red wine"></div>
  <div class="hero-badge">
    <div class="brand-name">Maranoola</div>
    <p>Sed ut perspiciatis unde omnis iste natus error sit voluptatem accusan tium doloremque</p>
    <a class="btn" href="#">Read More &#9656;</a>
  </div>
  <svg class="hero-wave" width="1200" height="100" viewBox="0 0 1200 100">
    <path d="M0 10 Q600 150 1200 10 L1200 100 L0 100 Z" fill="#fff"/>
    <path d="M0 22 Q600 162 1200 22" fill="none" stroke="#2d8fd5" stroke-width="5"/>
  </svg>
</section>

<section class="section welcome">
  <h2 class="section-title">Welcome to Maranoola</h2>
  <p class="lead">Sed ut perspiciatis unde omnis iste natus error sit voluptatem accusantium doloremque laudantium, totam rem aperiam, eaque ipsa quae ab illo inventore veritatis et quasi architecto beatae vitae dicta sunt explicabo. Nemo enim ipsam voluptatem quia voluptas sit aspernatur aut odit aut fugit, sed quia consequuntur magni dolores eos qui ratione voluptatem sequi nesciunt. Neque porro quisquam est, qui dolorem ipsum quia dolor sit amet, consectetur</p>
  <div class="features">
    <div class="feature">
      <svg width="60" height="60" viewBox="0 0 60 60"><path d="M6 32 H54 Q52 52 30 52 Q8 52 6 32 Z" fill="#1f63b8"/><path d="M22 30 L30 8 M30 30 L36 6 M38 30 L44 12" stroke="#1f63b8" stroke-width="3"/></svg>
      <h3>Best Favorite</h3>
      <p>Sed ut perspiciatis unde omnis iste natus error sit voluptatem accusantium doloremque laudantium, totam rem aperiam, eaque ipsa quae</p>
    </div>
    <div class="feature">
      <svg width="60" height="60" viewBox="0 0 60 60"><g fill="#1f63b8"><circle cx="18" cy="22" r="6"/><circle cx="30" cy="22" r="6"/><circle cx="42" cy="22" r="6"/><circle cx="24" cy="33" r="6"/><circle cx="36" cy="33" r="6"/><circle cx="30" cy="44" r="6"/></g><path d="M30 16 Q34 6 46 6" stroke="#1f63b8" stroke-width="3" fill="none"/></svg>
      <h3>Best Grapes</h3>
      <p>Sed ut perspiciatis unde omnis iste natus error sit voluptatem accusantium doloremque laudantium, totam rem aperiam, eaque ipsa quae</p>
    </div>
    <div class="feature">
      <svg width="60" height="60" viewBox="0 0 60 60"><rect x="8" y="28" width="44" height="26" fill="#1f63b8"/><rect x="18" y="6" width="8" height="22" fill="#1f63b8"/><rect x="34" y="6" width="8" height="22" fill="#1f63b8"/></svg>
      <h3>Good Taste</h3>
      <p>Sed ut perspiciatis unde omnis iste natus error sit voluptatem accusantium doloremque laudantium, totam rem aperiam, eaque ipsa quae</p>
    </div>
  </div>
</section>

<section class="section delivery">
  <div class="delivery-photo" role="img" aria-label="Dim close-up of hands working with grapes"></div>
  <div class="delivery-inner">
    <h2>Delivery charge is <span class="price">$14.90</span> per<br>case Australia wide</h2>
    <p>Sed ut perspiciatis unde omnis iste natus error sit voluptatem accusantium doloremque laudantium, totam rem aperiam, eaque ipsa quae ab illo inventore veritatis et quasi architecto beatae vitae dicta sunt explicabo. Nemo enim ipsam voluptatem quia voluptas sit aspernatur</p>
    <a class="btn" href="#">Read More</a>
  </div>
</section>

<section class="section products">
  <div class="product-photo" role="img" aria-label="Bottle of Maranoola white wine beside a bowl of red crayfish"></div>
  <div class="product-body">
    <h2>Wine Products</h2>
    <p>Nemo enim ipsam voluptatem quia voluptas sit aspernatur aut odit aut fugit, sed quia consequuntur magni dolores eos qui ratione voluptatem sequi nesciunt. Neque porro quisquam est, qui dolorem ipsum quia dolor sit amet, consectetur, adipisci velit, sed quia non numquam eius modi tempora incidunt ut labore et dolore magnam aliquam quaerat voluptatem. Ut enim ad minima veniam, quis nostrum exercitationem</p>
    <ul class="tick-list">
      <li><svg width="12" height="12" viewBox="0 0 12 12"><circle cx="6" cy="6" r="6" fill="#1f63b8"/><path d="M3 6 L5.2 8 L9 4" stroke="#fff" stroke-width="1.5" fill="none"/></svg>Ut enim ad minima veniam, quis</li>
      <li><svg width="12" height="12" viewBox="0 0 12 12"><circle cx="6" cy="6" r="6" fill="#1f63b8"/><path d="M3 6 L5.2 8 L9 4" stroke="#fff" stroke-width="1.5" fill="none"/></svg>Nemo enim ipsam voluptatem quia voluptas</li>
      <li><svg width="12" height="12" viewBox="0 0 12 12"><circle cx="6" cy="6" r="6" fill="#1f63b8"/><path d="M3 6 L5.2 8 L9 4" stroke="#fff" stroke-width="1.5" fill="none"/></svg>Sed ut perspiciatis unde omnis iste</li>
      <li><svg width="12" height="12" viewBox="0 0 12 12"><circle cx="6" cy="6" r="6" fill="#1f63b8"/><path d="M3 6 L5.2 8 L9 4" stroke="#fff" stroke-width="1.5" fill="none"/></svg>Sed ut perspiciatis unde omnis iste</li>
    </ul>
    <a class="btn btn-solid" href="#">Book Now</a>
  </div>
</section>

<section class="section why">
  <h2 class="section-title">Why Us?</h2>
  <div class="cards">
    <article class="card">
      <div class="card-photo" role="img" aria-label="Picker holding a bucket of grapes among green vines" style="background:linear-gradient(180deg,#c9d3dc 0%,#8a9a6a 45%,#5a4a3a 100%)"></div>
      <h3>Wine Diploma Classes</h3>
      <p>Sed ut perspiciatis unde omnis iste natus error sit voluptatem accusantium doloremque</p>
    </article>
    <article class="card">
      <div class="card-photo" role="img" aria-label="Winemaker tipping a bin of grapes at the vineyard" style="background:linear-gradient(180deg,#b9c4cc 0%,#7d8c6a 40%,#7a6a5a 100%)"></div>
      <h3>Wine Studies</h3>
      <p>Sed ut perspiciatis unde omnis iste natus error sit voluptatem accusantium doloremque</p>
    </article>
    <article class="card">
      <div class="card-photo" role="img" aria-label="Family group gathered in the barrel cellar" style="background:linear-gradient(180deg,#3a3024 0%,#6b5540 50%,#2a2218 100%)"></div>
      <h3>Wine Certificate Classes</h3>
      <p>Sed ut perspiciatis unde omnis iste natus error sit voluptatem accusantium doloremque</p>
    </article>
  </div>
</section>

<section class="section gallery-news">
  <h2 class="block-title gallery-title">Our Gallery</h2>
  <div class="gallery-grid">
    <div class="thumb" style="top:0;background:linear-gradient(160deg,#6f8a4a,#3f5a2a)" role="img" aria-label="Pickers among the vines"></div>
    <div class="thumb" style="top:97px;background:linear-gradient(160deg,#b08a5a,#6a7a8a)" role="img" aria-label="Harvest crew group outdoors"></div>
    <div class="thumb" style="top:194px;background:linear-gradient(160deg,#8a8a80,#4a4a44)" role="img" aria-label="Work in the winery shed"></div>
    <div class="feature-shot" style="background:linear-gradient(150deg,#6a6a66 0%,#8a3a3a 50%,#5a1a22 100%)" role="img" aria-label="Family foot crushing grapes in a large tub"></div>
  </div>
  <h2 class="block-title news-title">Latest News</h2>
  <div class="news">
    <article class="news-item">
      <div class="news-photo" style="background:linear-gradient(180deg,#6a7a5a,#3a2f24)" role="img" aria-label="Vines at harvest"></div>
      <div>
        <h4>Nemo Enim Ipsam Volup</h4>
        <div class="news-date"><svg width="11" height="11" viewBox="0 0 12 12"><circle cx="6" cy="6" r="5" fill="none" stroke="#1f63b8" stroke-width="1.5"/><path d="M6 3 V6 H8.5" stroke="#1f63b8" stroke-width="1.5" fill="none"/></svg>15 July 2017</div>
        <p>Vivamus elementum semper nisi. Lorem ipsum dolor sit amet, sectetuer adipiscing elit.</p>
      </div>
    </article>
    <article class="news-item">
      <div class="news-photo" style="background:linear-gradient(180deg,#4a3a2a,#b89a3a 60%,#3a3024)" role="img" aria-label="Forklift moving bins in the winery"></div>
      <div>
        <h4>Nemo Enim Ipsam Volup</h4>
        <div class="news-date"><svg width="11" height="11" viewBox="0 0 12 12"><circle cx="6" cy="6" r="5" fill="none" stroke="#1f63b8" stroke-width="1.5"/><path d="M6 3 V6 H8.5" stroke="#1f63b8" stroke-width="1.5" fill="none"/></svg>15 July 2017</div>
        <p>Vivamus elementum semper nisi. Lorem ipsum dolor sit amet, sectetuer adipiscing elit.</p>
      </div>
    </article>
  </div>
</section>

<footer class="section site-footer">
  <div class="footer-col" style="left:98px">
    <div class="footer-brand">Maranoola</div>
    <p class="footer-address">Maranoola 4102, Unit 12,<br>Brookmere Rd, SA</p>
    <div class="contact-row">
      <svg width="18" height="18" viewBox="0 0 18 18"><path d="M4 2 L7 2 L8 6 L6 7.5 Q8 11 10.5 12 L12 10 L16 11 L16 14 Q9 16 4 9 Q2 5 4 2 Z" fill="none" stroke="#fff" stroke-width="1.3"/></svg>
      <span>Call Us +61 8 8800 1234<br>(08) - 8800 - 5678</span>
    </div>
    <div class="contact-row">
      <svg width="18" height="14" viewBox="0 0 18 14"><rect x="1" y="1" width="16" height="12" fill="none" stroke="#fff" stroke-width="1.3"/><path d="M1 1 L9 8 L17 1" fill="none" stroke="#fff" stroke-width="1.3"/></svg>
      <span>info@maranoolawines-example.com</span>
    </div>
  </div>
  <div class="footer-col" style="left:419px">
    <h4>Quick Links</h4>
    <ul class="quick-links">
      <li>Home</li><li>About Maranoola</li><li>Products</li><li>Our Gallery</li><li>Manufacturers</li><li>Blog</li><li>Contact Us</li>
    </ul>
  </div>
  <div class="footer-col newsletter" style="left:640px">
    <h4>Join Our Newsletter</h4>
    <p>Excepteur sint occaecat cupidatat non proident, sunt in culpa qui</p>
    <div class="field">Enter Name</div>
    <a class="btn btn-dark" href="#">Subscribe</a>
  </div>
  <div class="footer-col" style="left:1003px">
    <h4>Social</h4>
    <ul class="social-list">
      <li><span class="dot"></span>Vinebook</li>
      <li><span class="dot"></span>Chirpline</li>
      <li><span class="dot"></span>Harvest+</li>
      <li><span class="dot"></span>vineclips</li>
    </ul>
  </div>
  <div class="footer-bar">2017 &copy; Copyrights Maranoola.All Rights Reserved<span class="page-tag">C7</span></div>
</footer>

</body>
</html>
```